Rollers & Glides.com

Vertical Business Card with focus on branding with our icon. Information on card will be logo, persons name, position, phone number, email address and website. Use the the name Marcus Pellow, position President, phone number 480.915.2267, email Marcus@rollersandglides-demo.com, website www.rollersandglides-demo.com.

```html
<!DOCTYPE html>
<html lang="en">
<head>
<meta charset="utf-8">
<title>Rollers &amp; Glides.com — Business Card</title>
<link rel="stylesheet" href="https://fonts.googleapis.com/css2?family=Montserrat:wght@800&family=Roboto:wght@400;500&display=swap">
<style>
  :root {
    --backdrop: #cfd3d5;
    --card-white: #ecebe8;
    --brand-navy: #14267a;
    --brand-blue: #1f49a8;
    --brand-blue-light: #3a63c4;
    --ink: #222428;
    --white: #ffffff;
  }
  * { margin: 0; padding: 0; box-sizing: border-box; }
  html, body {
    width: 1200px;
    height: 1049px;
    overflow: hidden;
    background: var(--backdrop);
  }
  .canvas {
    position: relative;
    width: 1200px;
    height: 1049px;
    display: flex;
    justify-content: center;
    align-items: center;
    gap: 100px;
  }
  .card {
    position: relative;
    width: 400px;
    height: 700px;
    border-radius: 4px;
    overflow: hidden;
    box-shadow: 0 18px 40px rgba(40, 45, 50, 0.25);
  }

  /* Front */
  .card-front {
    background: var(--card-white);
    border-bottom: 3px solid var(--brand-blue);
    padding: 72px 0 0 58px;
  }
  .person-name {
    font-family: "Montserrat", sans-serif;
    font-weight: 800;
    font-size: 29px;
    letter-spacing: 0.5px;
    color: var(--brand-navy);
    text-transform: uppercase;
    line-height: 1.1;
  }
  .person-role {
    font-family: "Roboto", sans-serif;
    font-weight: 500;
    font-size: 20px;
    color: var(--ink);
    margin-top: 4px;
  }
  .divider {
    width: 30px;
    height: 3px;
    background: var(--brand-navy);
    margin: 22px 0 16px;
  }
  .contact-list { list-style: none; }
  .contact-item {
    display: flex;
    align-items: center;
    gap: 10px;
    font-family: "Roboto", sans-serif;
    font-size: 16.5px;
    color: var(--ink);
    line-height: 1;
    margin-bottom: 13px;
    white-space: nowrap;
  }
  .contact-icon { width: 16px; height: 16px; flex: none; }
  .brand-name {
    position: absolute;
    left: 0;
    right: 0;
    top: 470px;
    display: flex;
    justify-content: center;
    align-items: center;
    gap: 12px;
    font-family: "Montserrat", sans-serif;
    font-weight: 800;
    font-size: 26px;
    color: var(--brand-navy);
  }
  .brand-dot {
    width: 18px;
    height: 18px;
    border-radius: 50%;
    background: var(--brand-navy);
  }

  /* Back */
  .card-back {
    background: var(--brand-blue);
  }
  .back-pattern {
    position: absolute;
    inset: 0;
    background: linear-gradient(160deg, var(--brand-blue-light) 0%, var(--brand-blue) 55%, #1c44a0 100%);
  }
  .back-brand {
    position: absolute;
    left: 0;
    right: 0;
    bottom: 90px;
    text-align: center;
    font-family: "Montserrat", sans-serif;
    font-weight: 800;
    font-size: 22px;
    color: var(--white);
  }
</style>
</head>
<body>
<main class="canvas">

  <section class="card card-front" aria-label="Business card front">
    <h1 class="person-name">Marcus Pellow</h1>
    <p class="person-role">President</p>
    <div class="divider"></div>
    <ul class="contact-list">
      <li class="contact-item">
        <svg class="contact-icon" viewBox="0 0 16 16" aria-hidden="true">
          <path d="M2 5c0-2 2-3 6-3s6 1 6 3v1h-3V5H5v1H2z M4 7h8l2 7H2z" fill="#14267a"/>
        </svg>
        480.915.2267
      </li>
      <li class="contact-item">
        <svg class="contact-icon" viewBox="0 0 16 16" aria-hidden="true">
          <rect x="1" y="3" width="14" height="10" fill="#14267a"/>
          <path d="M1 3l7 6 7-6" fill="none" stroke="#ecebe8" stroke-width="1.2"/>
        </svg>
        Marcus@rollersandglides-demo.com
      </li>
      <li class="contact-item">
        <svg class="contact-icon" viewBox="0 0 16 16" aria-hidden="true">
          <circle cx="8" cy="8" r="7" fill="#14267a"/>
          <path d="M1 8h14 M8 1c-3 3-3 11 0 14 M8 1c3 3 3 11 0 14" fill="none" stroke="#ecebe8" stroke-width="0.9"/>
        </svg>
        www.rollersandglides-demo.com
      </li>
    </ul>
    <div class="brand-name"><span class="brand-dot"></span>Rollers &amp; Glides.com</div>
  </section>

  <section class="card card-back" aria-label="Business card back">
    <div class="back-pattern" role="img" aria-label="Repeating embossed brand pattern across the blue card back"></div>
    <div class="back-brand">Rollers &amp; Glides.com</div>
  </section>

</main>
</body>
</html>
```